Velmora Freightway Solutions Business cards

Would like a very unique design catchy but professional for business cards. Please use log provided.Marlon WellsCeo and Founder TransCon Logistix Solutions1-888-913-3225mwells@tlsolutionsus.comwww.tlsolutionsus.com

```html
<!DOCTYPE html>
<html lang="en">
<head>
<meta charset="utf-8">
<title>Velmora Freightway Solutions – Business Cards</title>
<link rel="stylesheet" href="https://fonts.googleapis.com/css2?family=Montserrat:wght@500;600&family=Open+Sans:wght@400;600&display=swap">
<style>
  :root {
    --brand-blue: #1170bb;
    --brand-red: #e3202a;
    --card-white: #ffffff;
    --backdrop: #2a2a2e;
    --wordmark-font: "Montserrat", sans-serif;
    --body-font: "Open Sans", sans-serif;
  }
  * { margin: 0; padding: 0; box-sizing: border-box; }
  html, body { width: 1200px; height: 800px; overflow: hidden; }
  body { background: var(--backdrop); position: relative; font-family: var(--body-font); }

  .card {
    position: absolute;
    width: 600px;
    height: 343px;
    overflow: hidden;
    box-shadow: 0 18px 40px rgba(0,0,0,0.45);
  }

  /* Front */
  .card-front { left: 70px; top: 50px; background: var(--brand-blue); }
  .card-front .wordmark {
    position: absolute; left: 0; right: 0; top: 138px;
    display: flex; align-items: center; justify-content: center; gap: 12px;
  }
  .mark-square { width: 22px; height: 22px; background: var(--card-white); }
  .wordmark-text {
    font-family: var(--wordmark-font); font-weight: 600; font-size: 24px;
    letter-spacing: 2px; text-transform: uppercase; color: var(--card-white);
  }
  .card-front .wordmark-rule {
    position: absolute; left: 150px; right: 150px; top: 186px;
    height: 2px; background: var(--brand-red);
  }

  /* Back */
  .card-back { left: 530px; top: 405px; background: var(--card-white); }
  .card-back .wordmark { position: absolute; left: 0; right: 0; top: 48px;
    display: flex; align-items: center; justify-content: center; gap: 10px; }
  .card-back .mark-square { background: var(--brand-blue); width: 18px; height: 18px; }
  .card-back .wordmark-text { color: var(--brand-blue); font-size: 20px; }
  .card-back .wordmark-rule {
    position: absolute; left: 170px; right: 170px; top: 86px;
    height: 1.5px; background: var(--brand-red);
  }

  .person { position: absolute; left: 0; right: 0; top: 150px; text-align: center; }
  .person-name { font-size: 24px; color: var(--brand-blue); line-height: 1.1; }
  .person-title { font-size: 14px; color: var(--brand-red); }

  .divider { position: absolute; height: 1px; background: var(--brand-red); }
  .divider-left { left: 24px; width: 200px; top: 222px; }
  .divider-right { right: 24px; width: 200px; top: 150px; }

  .company-block { position: absolute; right: 28px; top: 160px; text-align: right; }
  .company-name { font-size: 14px; color: var(--brand-red); }
  .company-web { font-size: 13px; color: var(--brand-blue); }

  .contact-list { position: absolute; left: 28px; top: 240px; list-style: none; }
  .contact-list li {
    display: flex; align-items: center; gap: 8px;
    font-size: 14px; color: var(--brand-blue); margin-bottom: 6px;
  }
  .contact-icon { width: 18px; height: 18px; flex: none; }

  .edge-band { position: absolute; left: 0; right: 0; bottom: 0; height: 10px; display: flex; }
  .edge-band-blue { flex: 0 0 60%; background: var(--brand-blue); }
  .edge-band-red { flex: 1; background: var(--brand-red); }
</style>
</head>
<body>

<section class="card card-front" aria-label="Card front">
  <div class="wordmark">
    <span class="mark-square"></span>
    <span class="wordmark-text">Velmora Freightway Solutions</span>
  </div>
  <div class="wordmark-rule"></div>
</section>

<section class="card card-back" aria-label="Card back">
  <div class="wordmark">
    <span class="mark-square"></span>
    <span class="wordmark-text">Velmora Freightway Solutions</span>
  </div>
  <div class="wordmark-rule"></div>

  <div class="person">
    <p class="person-name">Dorian Pike</p>
    <p class="person-title">Ceo and Founder</p>
  </div>

  <div class="divider divider-right"></div>
  <div class="company-block">
    <p class="company-name">Velmora Freightway Solutions</p>
    <p class="company-web">www.vfwayroutes.com</p>
  </div>

  <div class="divider divider-left"></div>
  <ul class="contact-list">
    <li>
      <svg class="contact-icon" viewBox="0 0 18 18" aria-hidden="true">
        <circle cx="9" cy="9" r="9" fill="#e3202a"/>
        <rect x="6" y="4" width="6" height="10" rx="1" fill="none" stroke="#fff" stroke-width="1.3"/>
        <circle cx="9" cy="12" r="0.8" fill="#fff"/>
      </svg>
      1-888-470-6158
    </li>
    <li>
      <svg class="contact-icon" viewBox="0 0 18 18" aria-hidden="true">
        <circle cx="9" cy="9" r="9" fill="#e3202a"/>
        <rect x="4.5" y="5.5" width="9" height="7" fill="none" stroke="#fff" stroke-width="1.2"/>
        <path d="M4.5 5.5 L9 9.5 L13.5 5.5" fill="none" stroke="#fff" stroke-width="1.2"/>
      </svg>
      dpike@vfwayroutes.com
    </li>
  </ul>

  <div class="edge-band">
    <span class="edge-band-blue"></span>
    <span class="edge-band-red"></span>
  </div>
</section>

</body>
</html>
```